Aerial Imaging and photgraphy business card

Design a business card with eye catching aerial photo of country side / landscape with a drone in the foreground.
Also contact details.

Target Market(s)

Aerial Imaging photography

Industry/Entity Type

Advertising

Contact Information for Business Card

Rowland
0412965203
Website http://www.skywardvistaphoto.com.au/
email address : skywardvistaphoto.com.au

Colors
e8f1ca
cadf82
9bcb3c
33a6d7
85cae6
cee9f5

Requirements
Must have
• High res photo
• Korvane drone in the foreground Either T4200 and korvane Glidewing or both
Nice to have
• high resolution landscape country photo on the front of the card with a Korvane T4200 drone in the foreground.

```html
<!DOCTYPE html>
<html lang="en">
<head>
<meta charset="utf-8">
<title>Skyward Vista Photo – Business Card</title>
<link href="https://fonts.googleapis.com/css2?family=Montserrat:wght@400;600;700&display=swap" rel="stylesheet">
<style>
  :root {
    --backdrop: #2b2c2e;
    --card-white: #ffffff;
    --ink-dark: #2a2a2a;
    --brand-blue: #33a6d7;
    --sky-light: #85cae6;
    --sky-pale: #cee9f5;
    --field-green: #9bcb3c;
    --text-light: #ffffff;
    --divider: rgba(255,255,255,0.75);
  }
  * { box-sizing: border-box; margin: 0; padding: 0; }
  html, body {
    width: 1200px; height: 900px; overflow: hidden;
    background: var(--backdrop);
    font-family: "Montserrat", Arial, sans-serif;
  }
  .canvas { position: relative; width: 1200px; height: 900px; }

  .card {
    position: absolute;
    width: 560px; height: 320px;
    border-radius: 22px;
    overflow: hidden;
    box-shadow: 0 18px 40px rgba(0,0,0,0.45);
  }

  /* Back card */
  .card--back { left: 110px; top: 100px; background: var(--card-white); }
  .card--back .brand {
    position: absolute; left: 0; right: 0; top: 112px;
    display: flex; justify-content: center; align-items: center; gap: 12px;
  }
  .brand-dot { width: 22px; height: 22px; border-radius: 50%; background: var(--brand-blue); flex: none; }
  .brand-name { font-weight: 700; font-size: 30px; color: var(--ink-dark); letter-spacing: 0.5px; }
  .card--back .site {
    position: absolute; left: 0; right: 0; bottom: 36px;
    text-align: center; font-size: 15px; color: var(--ink-dark);
  }
  .accent { color: var(--brand-blue); }

  /* Front card */
  .card--front { left: 530px; top: 480px; }
  .photo {
    position: absolute; inset: 0;
    background: linear-gradient(180deg, #5d7486 0%, #7c93a3 28%, #55705a 52%, #34502e 72%, #1c2a1c 100%);
  }
  .card--front .brand {
    position: absolute; left: 24px; top: 120px; width: 206px;
    display: flex; flex-direction: column; align-items: center; gap: 10px;
    text-align: center;
  }
  .card--front .brand-name {
    color: var(--text-light); font-size: 22px; line-height: 1.2; letter-spacing: 0.3px;
  }
  .divider {
    position: absolute; left: 248px; top: 86px;
    width: 1.5px; height: 150px; background: var(--divider);
  }
  .contact { position: absolute; left: 268px; top: 96px; width: 280px; color: var(--text-light); }
  .person-name { font-weight: 600; font-size: 24px; color: var(--brand-blue); }
  .person-role { font-size: 14px; margin-top: 2px; margin-bottom: 12px; }
  .contact-list { list-style: none; }
  .contact-list li {
    display: flex; align-items: center; gap: 8px;
    font-size: 14px; line-height: 22px; white-space: nowrap;
  }
  .contact-list svg { width: 12px; height: 12px; flex: none; }
</style>
</head>
<body>
<main class="canvas">
  <section class="card card--back">
    <div class="brand">
      <span class="brand-dot"></span>
      <span class="brand-name">Skyward Vista Photo</span>
    </div>
    <p class="site">www.<span class="accent">skywardvistaphoto</span>.com.au</p>
  </section>

  <section class="card card--front">
    <div class="photo" role="img" aria-label="Aerial photograph of green countryside and a lake under a pale sky, with a multi-rotor camera drone hovering in the foreground"></div>
    <div class="brand">
      <span class="brand-dot"></span>
      <span class="brand-name">Skyward Vista<br>Photo</span>
    </div>
    <div class="divider"></div>
    <div class="contact">
      <h1 class="person-name">Devin Rowland</h1>
      <p class="person-role">Director</p>
      <ul class="contact-list">
        <li>
          <svg viewBox="0 0 12 12"><path d="M3 1 L5 3.5 L4 5 Q5.5 7 7 8 L8.5 7 L11 9 L10 11 Q5 11 1 2 Z" fill="var(--brand-blue)"/></svg>
          <span>041 296 5203</span>
        </li>
        <li>
          <svg viewBox="0 0 12 12"><circle cx="6" cy="6" r="5" fill="none" stroke="var(--brand-blue)" stroke-width="1.3"/><path d="M1 6 H11 M6 1 Q3 6 6 11 Q9 6 6 1" fill="none" stroke="var(--brand-blue)" stroke-width="1"/></svg>
          <span>www.<span class="accent">skywardvistaphoto</span>.com.au</span>
        </li>
        <li>
          <svg viewBox="0 0 12 12"><rect x="1" y="2.5" width="10" height="7" fill="none" stroke="var(--brand-blue)" stroke-width="1.3"/><path d="M1 2.5 L6 6.5 L11 2.5" fill="none" stroke="var(--brand-blue)" stroke-width="1.1"/></svg>
          <span>info@skywardvistaphoto.com.au</span>
        </li>
      </ul>
    </div>
  </section>
</main>
</body>
</html>
```